Bold and colurful E-liquid Design Template

I'm looking for a new label for my house range of vape e-liquids. I currently have almost 40 flavours, so I'm looking for a single label design that I can modify to create the rest of the flavours.
Each label will have the same design, but I'll change the color for each flavour and the name.
I'd like the label to be predominantly text based with bold text and bold colours. I like bold typographic styles. Also for each flavour I'd like to add 1 - 3 letters to represent the flavour. This can be in a larger font.
eg for
Blueberry I'll use the letter B
Pineapple Peach will use PP
Cinnamon Blueberry Muffin uses RVB
The colour used on the label will also be important so they stand out nicely on the shelf.
I've attached a psd mockup of the bottles I'll be using.

```html
<!DOCTYPE html>
<html lang="en">
<head>
<meta charset="utf-8">
<title>Vape E-Liquids – Flavour Label Range</title>
<link rel="stylesheet" href="https://fonts.googleapis.com/css2?family=Archivo+Black&family=Oswald:wght@700&display=swap">
<style>
  :root {
    --backdrop: #5f6064;
    --label-white: #ffffff;
    --spec-grey: #6b6c70;
    --plum: #9b1b5a;
    --amber: #f0a43a;
    --sky: #29a3dc;
  }
  html, body {
    margin: 0;
    padding: 0;
    width: 1098px;
    height: 1200px;
    overflow: hidden;
    background: var(--backdrop);
  }
  .label-range {
    position: relative;
    width: 1098px;
    height: 1200px;
    display: flex;
    justify-content: center;
    align-items: center;
    gap: 49px;
  }
  .flavour-label {
    width: 300px;
    height: 880px;
    display: block;
  }
  .flavour-label--plum { --accent: var(--plum); }
  .flavour-label--amber { --accent: var(--amber); }
  .flavour-label--sky { --accent: var(--sky); }

  .band { fill: var(--accent); }
  .label-body { fill: var(--label-white); }
  .brand-word,
  .range-word,
  .flavour-code {
    fill: var(--accent);
    font-family: "Archivo Black", "Arial Black", sans-serif;
  }
  .spec {
    fill: var(--spec-grey);
    font-family: "Oswald", "Arial Narrow", sans-serif;
    font-weight: 700;
  }
  .spec-rule { stroke: var(--spec-grey); stroke-width: 2; }
  .tagline {
    fill: var(--accent);
    font-family: "Oswald", "Arial Narrow", sans-serif;
    font-weight: 700;
  }
</style>
</head>
<body>
<main class="label-range">

  <svg class="flavour-label flavour-label--plum" viewBox="0 0 300 880" aria-label="Flavour label, plum">
    <rect class="band" x="0" y="0" width="300" height="105"/>
    <rect class="label-body" x="0" y="105" width="300" height="665"/>
    <rect class="band" x="0" y="770" width="300" height="110"/>
    <text class="brand-word" transform="translate(108,762) rotate(-90)" font-size="150" textLength="650" lengthAdjust="spacingAndGlyphs">VAPE</text>
    <text class="range-word" transform="translate(180,482) rotate(-90)" font-size="64" textLength="362" lengthAdjust="spacingAndGlyphs">E-LIQUIDS</text>
    <text class="spec" x="268" y="222" font-size="150" text-anchor="middle" textLength="50" lengthAdjust="spacingAndGlyphs">3</text>
    <text class="spec" x="266" y="310" font-size="52" text-anchor="middle" textLength="48" lengthAdjust="spacingAndGlyphs">MG</text>
    <line class="spec-rule" x1="208" y1="326" x2="290" y2="326"/>
    <text class="spec" x="247" y="420" font-size="98" text-anchor="middle" textLength="86" lengthAdjust="spacingAndGlyphs">100</text>
    <text class="spec" x="268" y="475" font-size="52" text-anchor="middle" textLength="42" lengthAdjust="spacingAndGlyphs">ML</text>
    <text class="flavour-code" x="220" y="672" font-size="58" text-anchor="middle" textLength="122" lengthAdjust="spacingAndGlyphs">RVB</text>
    <text class="tagline" x="147" y="758" font-size="19" textLength="148" lengthAdjust="spacingAndGlyphs">PREMIUM E-LIQUID</text>
  </svg>

  <svg class="flavour-label flavour-label--amber" viewBox="0 0 300 880" aria-label="Flavour label, amber">
    <rect class="band" x="0" y="0" width="300" height="105"/>
    <rect class="label-body" x="0" y="105" width="300" height="665"/>
    <rect class="band" x="0" y="770" width="300" height="110"/>
    <text class="brand-word" transform="translate(108,762) rotate(-90)" font-size="150" textLength="650" lengthAdjust="spacingAndGlyphs">VAPE</text>
    <text class="range-word" transform="translate(180,482) rotate(-90)" font-size="64" textLength="362" lengthAdjust="spacingAndGlyphs">E-LIQUIDS</text>
    <text class="spec" x="268" y="222" font-size="150" text-anchor="middle" textLength="50" lengthAdjust="spacingAndGlyphs">3</text>
    <text class="spec" x="266" y="310" font-size="52" text-anchor="middle" textLength="48" lengthAdjust="spacingAndGlyphs">MG</text>
    <line class="spec-rule" x1="208" y1="326" x2="290" y2="326"/>
    <text class="spec" x="247" y="420" font-size="98" text-anchor="middle" textLength="86" lengthAdjust="spacingAndGlyphs">100</text>
    <text class="spec" x="268" y="475" font-size="52" text-anchor="middle" textLength="42" lengthAdjust="spacingAndGlyphs">ML</text>
    <text class="flavour-code" x="220" y="672" font-size="58" text-anchor="middle" textLength="122" lengthAdjust="spacingAndGlyphs">RVB</text>
    <text class="tagline" x="147" y="758" font-size="19" textLength="148" lengthAdjust="spacingAndGlyphs">PREMIUM E-LIQUID</text>
  </svg>

  <svg class="flavour-label flavour-label--sky" viewBox="0 0 300 880" aria-label="Flavour label, sky blue">
    <rect class="band" x="0" y="0" width="300" height="105"/>
    <rect class="label-body" x="0" y="105" width="300" height="665"/>
    <rect class="band" x="0" y="770" width="300" height="110"/>
    <text class="brand-word" transform="translate(108,762) rotate(-90)" font-size="150" textLength="650" lengthAdjust="spacingAndGlyphs">VAPE</text>
    <text class="range-word" transform="translate(180,482) rotate(-90)" font-size="64" textLength="362" lengthAdjust="spacingAndGlyphs">E-LIQUIDS</text>
    <text class="spec" x="268" y="222" font-size="150" text-anchor="middle" textLength="50" lengthAdjust="spacingAndGlyphs">3</text>
    <text class="spec" x="266" y="310" font-size="52" text-anchor="middle" textLength="48" lengthAdjust="spacingAndGlyphs">MG</text>
    <line class="spec-rule" x1="208" y1="326" x2="290" y2="326"/>
    <text class="spec" x="247" y="420" font-size="98" text-anchor="middle" textLength="86" lengthAdjust="spacingAndGlyphs">100</text>
    <text class="spec" x="268" y="475" font-size="52" text-anchor="middle" textLength="42" lengthAdjust="spacingAndGlyphs">ML</text>
    <text class="flavour-code" x="220" y="672" font-size="58" text-anchor="middle" textLength="122" lengthAdjust="spacingAndGlyphs">RVB</text>
    <text class="tagline" x="147" y="758" font-size="19" textLength="148" lengthAdjust="spacingAndGlyphs">PREMIUM E-LIQUID</text>
  </svg>

</main>
</body>
</html>
```